Web Design job - Condo Debts Collection Business needs a Web Design

I need a site for a client, who works with condo debts collection, and ensure all revenues provided by condo fees will be always available to the building manager of condo on a specific date, regardless of defaults.
I have the visual identity (logo, slogan and colors) of the company, and some requirements on layout (kind of slider, menu options, phone number on a noble position, etc) - maybe I can do a sketch, but I like the idea of give some freedom to designer.

*** PLEASE, we have no interest in templates. We want something new***

Target Market(s)

I have two targets for this design: - Condominium's building manager. This target is looking for a solution to overdue debts on it's condo. - Residents on condominiums. This target wants to live in a better place, where their neighbors pay their condominium fees on time.

Number of Pages Required

1 page

Requirements
Must have
• - Slider with title, some short text related, a nice image (I prefer happy and/or peaceful family, people doing business, happy friends, and so on).
• - I have a special attention to menu. I'm looking for one I can have a nice effect, more elegant, charming, kind of innovative.
• - Phone number on the top (or clearly visible).
• - Member log in area or icon on the top (or clearly visible).
• - News/articles area.
• - Modern fonts, with good quality, sans-serif on areas where reading is more intensive (prefer Google web-fonts).
• - Colors specified on attached files.
Nice to have
• - Clear background color, cause it's better to read larger texts (like articles). Dark backgrounds makes reading difficult.
• - A site with effects (like shadows, lines, curves, gradients, lights) is usually pretty.
• - I pay attention on beautiful footers.
Should not have
• - Images with a lot of money (I don't sell richness, I sell tranquility, peace, harmony, safety).
• - Poor menu.

```html
<!DOCTYPE html>
<html lang="en">
<head>
<meta charset="utf-8">
<title>Solvant – Cobrança Condominial</title>
<link rel="stylesheet" href="https://fonts.googleapis.com/css2?family=Open+Sans:wght@400;600;700;800&family=Roboto+Slab:wght@700&display=swap">
<style>
:root{
  --gold:#e4a020;
  --gold-dark:#c98a10;
  --gold-light:#f3b93a;
  --ink:#222222;
  --text:#4a4a4a;
  --dark-panel:#262626;
  --white:#ffffff;
}
*{box-sizing:border-box;margin:0;padding:0}
html,body{width:1200px;height:2875px;overflow:hidden}
body{position:relative;background:var(--white);font-family:"Open Sans",Arial,sans-serif;color:var(--text)}
.abs{position:absolute}

/* header */
.brand{left:75px;top:12px;display:flex;align-items:center;gap:14px}
.brand-mark{width:58px;height:58px;background:var(--gold)}
.brand-name{font-family:"Open Sans",sans-serif;font-weight:800;font-size:50px;line-height:46px;color:var(--ink);letter-spacing:-1px}
.brand-tag{font-size:10px;font-weight:700;color:var(--ink);letter-spacing:.5px;margin-top:2px}
.call{left:782px;top:36px;font-weight:700;font-size:15px;color:var(--ink)}
.top-icons{left:990px;top:36px;display:flex;gap:20px;align-items:center}

/* nav */
.navbar{left:75px;top:90px;width:1065px;height:58px;display:flex;z-index:3}
.nav-gold{flex:1;background:linear-gradient(var(--gold-light),var(--gold));display:flex;align-items:stretch;padding-left:33px}
.nav-item{display:flex;align-items:center;padding:0 25px;font-size:15px;font-weight:600;color:var(--ink);text-transform:uppercase}
.nav-item.active{background:var(--white);font-weight:700;padding:0 26px}
.member{width:205px;background:var(--dark-panel);color:var(--white);display:flex;align-items:center;justify-content:center;gap:10px;font-size:15px;font-weight:600;text-transform:uppercase;clip-path:polygon(14px 0,100% 0,100% 100%,0 100%)}

/* hero */
.hero{left:0;top:90px;width:1200px;height:610px;background:linear-gradient(100deg,#8c8478 0%,#b49a80 30%,#a0704e 50%,#4b3f72 75%,#c8b9a0 100%)}
.hero-shade{left:0;top:90px;width:1200px;height:610px;background:linear-gradient(rgba(0,0,0,.05),rgba(0,0,0,.25))}
.hero-title{left:0;top:222px;width:1200px;text-align:center;font-size:150px;font-weight:700;color:rgba(255,255,255,.92);letter-spacing:2px;line-height:170px}
.hero-sub{left:0;top:402px;width:1200px;text-align:center;font-size:34px;font-weight:700;color:rgba(255,255,255,.9);letter-spacing:2px;text-transform:uppercase}
.hero-btn{left:488px;top:472px;width:224px;height:40px;border-radius:4px;background:var(--gold);color:var(--white);font-weight:700;font-size:17px;display:flex;align-items:center;justify-content:center;gap:14px;text-transform:uppercase}
.arrow{top:370px}
.hero-edge{left:0;top:600px;width:1200px;height:110px}

/* sections */
.section-title{left:0;width:1200px;text-align:center;font-family:"Roboto Slab",Georgia,serif;font-size:30px;color:var(--ink);text-transform:uppercase}
.lead{left:180px;width:840px;text-align:center;font-size:15px;line-height:25px}
.btn{height:40px;border-radius:4px;background:linear-gradient(var(--gold-light),var(--gold-dark));color:var(--ink);font-weight:700;font-size:15px;text-transform:uppercase;display:flex;align-items:center;justify-content:center;box-shadow:0 2px 3px rgba(0,0,0,.2)}
.service-title{font-family:"Roboto Slab",Georgia,serif;font-size:29px;color:var(--ink)}
.service-text{width:515px;font-size:15px;line-height:25px}
.service-visual{width:478px;height:410px}

/* articles */
.card{width:332px;height:345px;top:2037px}
.card-photo{position:absolute;left:0;top:0;width:332px;height:213px}
.card-body{position:absolute;left:19px;top:173px;width:296px;height:172px;background:var(--white);box-shadow:0 0 6px rgba(0,0,0,.2);text-align:center;padding:20px 18px 0}
.card-body p{font-size:14px;line-height:24px}
.card-body .btn{width:122px;height:32px;font-size:13px;margin:20px auto 0}

/* footer */
.footer{left:0;top:2420px;width:1200px;height:455px;background:linear-gradient(#f6f6f6,#e6e6e6)}
.footer-edge{left:0;top:2410px;width:1200px;height:100px}
.footer-brand{left:466px;top:2475px;display:flex;align-items:center;gap:14px}
.footer-brand .brand-mark{width:62px;height:62px}
.f-head{top:2593px;font-family:"Roboto Slab",Georgia,serif;font-size:15px;color:var(--ink);text-transform:uppercase}
.f-list{list-style:none;font-size:15px;line-height:28px;color:var(--ink)}
.f-list li{display:flex;align-items:center;gap:18px}
.contact li{gap:14px;align-items:flex-start}
.email-field{left:288px;top:2636px;width:272px;height:34px;background:var(--white);display:flex;align-items:center;justify-content:space-between;padding:0 14px;font-size:13px;color:var(--ink)}
.subscribe{left:288px;top:2681px;width:122px;height:32px;font-size:13px}
.socials{left:962px;top:2630px;display:flex;gap:12px}
.ring{width:34px;height:34px;border:2px solid var(--ink);border-radius:50%;display:flex;align-items:center;justify-content:center}
.copyright{left:0;top:2836px;width:1200px;text-align:center;font-size:13px;color:var(--ink)}
.copyright b{font-size:15px}
</style>
</head>
<body>

<!-- header -->
<div class="abs brand">
  <div class="brand-mark"></div>
  <div><div class="brand-name">solvant</div><div class="brand-tag">COBRANÇA CONDOMINIAL</div></div>
</div>
<div class="abs call">CALL US :1-800 555 0142</div>
<div class="abs top-icons">
  <svg width="16" height="16" viewBox="0 0 16 16"><circle cx="8" cy="8" r="6.5" fill="none" stroke="#222" stroke-width="1.6"/><path d="M1.5 8h13M8 1.5c-3 3.5-3 9.5 0 13M8 1.5c3 3.5 3 9.5 0 13" fill="none" stroke="#222" stroke-width="1.3"/></svg>
  <svg width="16" height="16" viewBox="0 0 16 16"><path d="M2 2h12v9H7l-3 3v-3H2z" fill="#222"/></svg>
  <svg width="16" height="16" viewBox="0 0 16 16"><circle cx="3.5" cy="8" r="2.2" fill="#222"/><circle cx="12.5" cy="3.5" r="2.2" fill="#222"/><circle cx="12.5" cy="12.5" r="2.2" fill="#222"/><path d="M3.5 8l9-4.5M3.5 8l9 4.5" stroke="#222" stroke-width="1.4"/></svg>
  <svg width="16" height="12" viewBox="0 0 16 12"><rect x="1" y="1" width="14" height="10" fill="none" stroke="#222" stroke-width="2"/><polyline points="1,1 8,7 15,1" fill="none" stroke="#222" stroke-width="2"/></svg>
</div>

<!-- hero -->
<div class="abs hero" role="img" aria-label="Smiling couple on a balcony of an apartment building"></div>
<div class="abs hero-shade"></div>

<nav class="abs navbar">
  <div class="nav-gold">
    <span class="nav-item active">Home</span>
    <span class="nav-item">About</span>
    <span class="nav-item">Services</span>
    <span class="nav-item">Articles</span>
    <span class="nav-item">Contact Us</span>
  </div>
  <div class="member">
    <svg width="16" height="16" viewBox="0 0 16 16"><circle cx="8" cy="5" r="3.5" fill="none" stroke="#fff" stroke-width="1.6"/><path d="M1.5 15c0-4 3-6 6.5-6s6.5 2 6.5 6z" fill="none" stroke="#fff" stroke-width="1.6"/></svg>
    Member Login
  </div>
</nav>

<div class="abs hero-title">SOLVANT</div>
<div class="abs hero-sub">Cobrança Condominial</div>
<div class="abs hero-btn">Get in touch
  <svg width="20" height="12" viewBox="0 0 20 12"><path d="M1 6h16M12 1l5 5-5 5" fill="none" stroke="#fff" stroke-width="2.4"/></svg>
</div>
<svg class="abs arrow" style="left:118px" width="20" height="30" viewBox="0 0 20 30"><path d="M16 3L4 15l12 12" fill="none" stroke="#fff" stroke-width="4"/></svg>
<svg class="abs arrow" style="left:1068px" width="20" height="30" viewBox="0 0 20 30"><path d="M4 3l12 12L4 27" fill="none" stroke="#fff" stroke-width="4"/></svg>

<svg class="abs hero-edge" viewBox="0 0 1200 110" preserveAspectRatio="none">
  <polygon points="0,20 600,80 1200,20 1200,110 0,110" fill="#fff"/>
  <polyline points="0,16 600,76 1200,16" fill="none" stroke="#e4a020" stroke-width="9"/>
</svg>

<!-- welcome -->
<h1 class="abs section-title" style="top:716px">Welcome</h1>
<p class="abs lead" style="top:762px">Maecenas pellentesque enim neque mi sed. Maecenas turpis neque blandit wisi fermentum congue at vivamus pharetra at placerat. Urna volutpat vitae nunc con eget. Mus sit mauris magna commodo lacus lorem pellentesque tempus. Fringilla duis habitant lacinia lorem eros tortor sed a. Repellendus nunc maxime.</p>
<div class="abs btn" style="left:530px;top:870px;width:140px">Read More</div>

<!-- services -->
<h2 class="abs section-title" style="top:950px">Services</h2>

<div class="abs service-visual" style="left:100px;top:1030px;background:linear-gradient(135deg,#e4a020 0%,#c9962e 40%,#5a524a 75%,#e9b028 100%)" role="img" aria-label="Collage of photos of a happy couple and family in warm yellow tones"></div>
<h3 class="abs service-title" style="left:614px;top:1102px">Condo debts collection</h3>
<p class="abs service-text" style="left:615px;top:1148px">Maecenas pellentesque enim neque mi sed. Maecenas turpis neque blandit wisi fermentum congue at vivamus pharetra at placerat. Urna volutpat vitae nunc con eget. Mus sit mauris magna commodo lacus lorem pellentesque tempus. Fringilla duis habitant lacinia lorem eros tortor sed a. Repellendus nunc maxime.</p>
<div class="abs btn" style="left:615px;top:1282px;width:150px">Read More</div>

<h3 class="abs service-title" style="left:74px;top:1568px">Amicable Debt Collections</h3>
<p class="abs service-text" style="left:75px;top:1614px">Maecenas pellentesque enim neque mi sed. Maecenas turpis neque blandit wisi fermentum congue at vivamus pharetra at placerat. Urna volutpat vitae nunc con eget. Mus sit mauris magna commodo lacus lorem pellentesque tempus. Fringilla duis habitant lacinia lorem eros tortor sed a. Repellendus nunc maxime.</p>
<div class="abs btn" style="left:75px;top:1746px;width:150px">Read More</div>

<div class="abs service-visual" style="left:635px;top:1492px;background:linear-gradient(135deg,#5a4a3e 0%,#f2b818 40%,#e9a826 65%,#2d2d2d 100%)" role="img" aria-label="Collage of apartment buildings and a garden path in yellow tones"></div>

<!-- articles -->
<h2 class="abs section-title" style="top:1953px">Articles</h2>

<article class="abs card" style="left:73px">
  <div class="card-photo" role="img" aria-label="Family in front of a modern house" style="background:linear-gradient(135deg,#a9b4b8,#d8d2c8 45%,#5d7a4a)"></div>
  <div class="card-body"><p>Placerat vehicula id suspendisse lorem eget. Vel et gravida. Non a dapibus eget scelerisque quisque.</p><div class="btn">Read More</div></div>
</article>
<article class="abs card" style="left:433px">
  <div class="card-photo" role="img" aria-label="Family looking at a tablet at home" style="background:linear-gradient(135deg,#c25a4a,#d9c7b8 45%,#3f5a8a)"></div>
  <div class="card-body"><p>Placerat vehicula id suspendisse lorem eget. Vel et gravida. Non a dapibus eget scelerisque quisque.</p><div class="btn">Read More</div></div>
</article>
<article class="abs card" style="left:793px">
  <div class="card-photo" role="img" aria-label="Family playing with soap bubbles outdoors" style="background:linear-gradient(135deg,#d9a860,#e8cf8a 45%,#6f8fbf)"></div>
  <div class="card-body"><p>Placerat vehicula id suspendisse lorem eget. Vel et gravida. Non a dapibus eget scelerisque quisque.</p><div class="btn">Read More</div></div>
</article>

<!-- footer -->
<footer>
  <div class="abs footer" role="img" aria-label="Faint line drawing of city buildings"></div>
  <svg class="abs footer-edge" viewBox="0 0 1200 100">
    <polygon points="0,0 1200,0 1200,90 600,10 0,90" fill="#fff"/>
    <polyline points="0,92 600,12 1200,92" fill="none" stroke="#e4a020" stroke-width="8"/>
  </svg>
  <div class="abs footer-brand">
    <div class="brand-mark"></div>
    <div><div class="brand-name">solvant</div><div class="brand-tag">COBRANÇA CONDOMINIAL</div></div>
  </div>

  <h4 class="abs f-head" style="left:77px">Quick Links</h4>
  <ul class="abs f-list" style="left:72px;top:2636px">
    <li><svg width="8" height="12" viewBox="0 0 8 12"><path d="M1 1l5 5-5 5" fill="none" stroke="#222" stroke-width="2"/></svg>Home</li>
    <li><svg width="8" height="12" viewBox="0 0 8 12"><path d="M1 1l5 5-5 5" fill="none" stroke="#222" stroke-width="2"/></svg>About Us</li>
    <li><svg width="8" height="12" viewBox="0 0 8 12"><path d="M1 1l5 5-5 5" fill="none" stroke="#222" stroke-width="2"/></svg>Services</li>
    <li><svg width="8" height="12" viewBox="0 0 8 12"><path d="M1 1l5 5-5 5" fill="none" stroke="#222" stroke-width="2"/></svg>Articles</li>
    <li><svg width="8" height="12" viewBox="0 0 8 12"><path d="M1 1l5 5-5 5" fill="none" stroke="#222" stroke-width="2"/></svg>Contact Us</li>
  </ul>

  <h4 class="abs f-head" style="left:288px">Newsletter Subscribe</h4>
  <div class="abs email-field">Enter Email id
    <svg width="14" height="10" viewBox="0 0 14 10"><rect x="1" y="1" width="12" height="8" fill="none" stroke="#222" stroke-width="1.5"/><polyline points="1,1 7,6 13,1" fill="none" stroke="#222" stroke-width="1.5"/></svg>
  </div>
  <div class="abs btn subscribe">Subscribe</div>

  <h4 class="abs f-head" style="left:648px">Contact Us</h4>
  <ul class="abs f-list contact" style="left:648px;top:2633px">
    <li><svg width="12" height="16" viewBox="0 0 12 16" style="margin-top:6px"><path d="M6 15C2 10 1 8 1 6a5 5 0 0 1 10 0c0 2-1 4-5 9z" fill="#222"/><circle cx="6" cy="6" r="2" fill="#efefef"/></svg><span>9870 Lorium ipsum,Dolor amit,<br>City name. country.</span></li>
    <li><svg width="12" height="14" viewBox="0 0 12 14" style="margin-top:7px"><path d="M2 1l3 3-1.5 2a8 8 0 0 0 4 4L9 8.5l3 3-2 2C5 13 0 8 0 3z" fill="#222"/></svg>+1 800 555 0187</li>
    <li><svg width="12" height="12" viewBox="0 0 12 12" style="margin-top:8px"><rect x="0" y="3" width="12" height="8" fill="#222"/><rect x="3" y="0" width="6" height="4" fill="#222"/></svg>+1 800 555 0163</li>
    <li><svg width="12" height="10" viewBox="0 0 12 10" style="margin-top:9px"><rect x="0" y="0" width="12" height="10" fill="#222"/><polyline points="0,0 6,5 12,0" fill="none" stroke="#efefef" stroke-width="1.2"/></svg>info@solvant-mail.com</li>
  </ul>

  <h4 class="abs f-head" style="left:962px">Follow Us</h4>
  <div class="abs socials">
    <span class="ring"><svg width="16" height="16" viewBox="0 0 16 16"><circle cx="8" cy="8" r="6.5" fill="none" stroke="#222" stroke-width="1.5"/><path d="M1.5 8h13M8 1.5c-3 3.5-3 9.5 0 13M8 1.5c3 3.5 3 9.5 0 13" fill="none" stroke="#222" stroke-width="1.2"/></svg></span>
    <span class="ring"><svg width="16" height="16" viewBox="0 0 16 16"><path d="M2 2h12v9H7l-3 3v-3H2z" fill="#222"/></svg></span>
    <span class="ring"><svg width="16" height="16" viewBox="0 0 16 16"><circle cx="3.5" cy="8" r="2.2" fill="#222"/><circle cx="12.5" cy="3.5" r="2.2" fill="#222"/><circle cx="12.5" cy="12.5" r="2.2" fill="#222"/><path d="M3.5 8l9-4.5M3.5 8l9 4.5" stroke="#222" stroke-width="1.4"/></svg></span>
    <span class="ring"><svg width="16" height="12" viewBox="0 0 16 12"><rect x="1" y="1" width="14" height="10" fill="none" stroke="#222" stroke-width="1.8"/><polyline points="1,1 8,7 15,1" fill="none" stroke="#222" stroke-width="1.8"/></svg></span>
  </div>

  <div class="abs copyright">© 2018 | <b>www.solvantcondominial.com</b></div>
</footer>

</body>
</html>
```